Brindle Children's Center - Child Care brochure

I just bought a new child care and completely renovated the space. We are also designing a new website, so I need the brochure to match that with updated info. www.brindlechildrenscenter.com - Information on there is current. We expect to have the new one up and running in the next few days. We have new photo's that I'd like to be added to the flyer too. ps. the boys in the pictures are mine, so i would appreciate one of them being added :). support@netcrafterhub.com has details on the website (dev.brindlechildrenscenter.com). The child care program is only open during the ski season - i.e. a resort facility catering to high end clients.
I'm attaching the the website information, the flyer I created, logo files and pictures.

Target Market(s)

Parents of young children

Font styles to use
Other font styles liked:
• "Things we said" & "Calibri Light"

Colors
cfeae6
fef1ee

Requirements
Must have
• Pictures of children. sleek design - winter, mountain theme. Check with website designer on new website.
Nice to have
• prices included
Should not have
• Kid like artwork

```html
<!DOCTYPE html>
<html lang="en">
<head>
<meta charset="utf-8">
<title>Brindle Children's Center – Brochure</title>
<link rel="stylesheet" href="https://fonts.googleapis.com/css2?family=Gochi+Hand&family=Open+Sans:wght@400;600;700&display=swap">
<style>
  :root {
    --stage: #e6eaeb;
    --teal: #8fd2cf;
    --teal-soft: #aee0dd;
    --teal-deep: #3f8f8b;
    --ink: #3d4a4d;
    --ink-soft: #5b6a6d;
    --paper: #eef6f6;
    --white-veil: rgba(255, 255, 255, 0.78);
    --blush: #fef1ee;
    --mint: #cfeae6;
  }
  * { box-sizing: border-box; margin: 0; padding: 0; }
  html, body { width: 1200px; height: 900px; overflow: hidden; }
  body {
    background: var(--stage);
    font-family: "Open Sans", Arial, sans-serif;
    color: var(--ink);
    position: relative;
  }
  .brochure {
    position: absolute;
    left: 120px; top: 130px;
    width: 960px; height: 640px;
    display: flex;
    background: var(--paper);
    box-shadow: 0 10px 30px rgba(40, 60, 65, 0.18);
    overflow: hidden;
  }
  .scenery {
    position: absolute; inset: 0;
    background:
      radial-gradient(ellipse 420px 200px at 20% 70%, #9fc2c3 0%, rgba(159,194,195,0) 70%),
      radial-gradient(ellipse 380px 160px at 55% 78%, #a9cdcd 0%, rgba(169,205,205,0) 70%),
      radial-gradient(ellipse 500px 260px at 70% 25%, #ffffff 0%, rgba(255,255,255,0) 70%),
      linear-gradient(180deg, #e4f2f2 0%, #cbe5e4 55%, #b7d9d8 100%);
  }
  .panel {
    position: relative;
    width: 320px; height: 100%;
    border-right: 1px solid rgba(255, 255, 255, 0.55);
  }
  .panel:last-child { border-right: none; }

  /* Left panel */
  .reservations {
    background: var(--teal);
    height: 250px;
    padding: 30px 30px 0;
  }
  .reservations h2 {
    font-size: 15px; font-weight: 700; margin-bottom: 10px;
  }
  .reservations p {
    font-size: 11.5px; line-height: 1.55; text-align: justify;
  }
  .reservations strong { font-weight: 700; }

  /* Middle panel */
  .rates-title {
    font-family: "Gochi Hand", cursive;
    font-size: 26px; color: var(--ink-soft);
    text-align: center; margin-top: 50px;
  }
  .bubble {
    position: absolute; left: 50%;
    width: 200px; height: 200px; border-radius: 50%;
    transform: translateX(-50%);
    text-align: center;
  }
  .bubble-daily {
    top: 108px; background: var(--teal-soft);
    padding-top: 38px;
  }
  .bubble-season {
    top: 292px; width: 210px; height: 210px;
    background: var(--white-veil);
    padding-top: 32px;
  }
  .price { font-size: 15px; font-weight: 700; color: var(--teal-deep); line-height: 1.1; }
  .price-note { font-size: 10px; color: var(--ink-soft); margin-bottom: 8px; }
  .season-head { font-size: 12.5px; line-height: 1.3; margin-bottom: 8px; }
  .season-grid {
    display: grid; grid-template-columns: 1fr 1fr; gap: 6px 12px;
    padding: 0 26px; text-align: left;
  }
  .season-grid .price-note { margin-bottom: 0; }
  .apres { margin-top: 6px; }

  /* Right panel */
  .name-mark {
    width: 170px; height: 170px; margin: 70px auto 0;
    border-radius: 50%; background: #ffffff;
    display: flex; align-items: center; justify-content: center;
    text-align: center; padding: 20px;
    font-size: 16px; font-weight: 700; color: var(--ink);
    line-height: 1.25;
  }
  .center-title {
    font-family: "Gochi Hand", cursive;
    font-size: 25px; color: var(--ink);
    text-align: center; margin-top: 24px;
  }
  .ages { font-size: 14px; text-align: center; line-height: 1.35; margin-top: 6px; }
  .hours {
    margin-top: 26px; background: var(--teal);
    text-align: center; padding: 8px 0 10px;
  }
  .hours .label { font-family: "Gochi Hand", cursive; font-size: 20px; color: var(--teal-deep); }
  .hours .time { font-size: 18px; font-weight: 700; color: var(--teal-deep); line-height: 1.1; }
  .contact {
    margin-top: 26px; text-align: center;
    font-size: 11.5px; color: var(--ink-soft); line-height: 1.55;
  }
  .contact .gap { margin-top: 10px; }
</style>
</head>
<body>
  <main class="brochure">
    <div class="scenery" role="img" aria-label="Photo of snowy mountain peaks under soft winter clouds"></div>

    <section class="panel panel-reservations">
      <div class="reservations">
        <h2>Reservations</h2>
        <p>We highly recommend making advanced reservations to guarantee your child's spot. Reservations can be made by phone <strong>801.555.0142</strong>, follow the reservations link or even e-mail us with reservation requests at <strong>reservations@brindlechildrenscenter.com</strong>. Reservations must be made at least 48 hours in advance.</p>
      </div>
    </section>

    <section class="panel panel-rates">
      <h2 class="rates-title">Rates</h2>
      <div class="bubble bubble-daily">
        <div class="price">$109</div><div class="price-note">full day</div>
        <div class="price">$89</div><div class="price-note">half day</div>
        <div class="price">$495</div><div class="price-note">five day package<br>(That's a $50 saving!)</div>
      </div>
      <div class="bubble bubble-season">
        <div class="season-head">NEW Season Ski<br>Pass Child Care Packages</div>
        <div class="season-grid">
          <div><div class="price">$900</div><div class="price-note">01-20 Full Days</div></div>
          <div><div class="price">$2,700</div><div class="price-note">41-60 Full Days</div></div>
          <div><div class="price">$1,800</div><div class="price-note">21-40 Full Days</div></div>
          <div><div class="price">$3,600</div><div class="price-note">60-80 Full Days</div></div>
        </div>
        <div class="apres"><div class="price">$30</div><div class="price-note">Après-ski care</div></div>
      </div>
    </section>

    <section class="panel panel-cover">
      <div class="name-mark">Brindle Children's Center</div>
      <h1 class="center-title">Brindle Children's Center</h1>
      <p class="ages">Serving children ages<br>6 wks thru 9 years</p>
      <div class="hours">
        <div class="label">Open daily</div>
        <div class="time">8:30-4:30</div>
      </div>
      <address class="contact" style="font-style: normal;">
        <div>P.O. Box 4127</div>
        <div>Brindle, Utah 84000</div>
        <div class="gap">(801) 555-0142</div>
        <div class="gap">info@brindlechildrenscenter.com</div>
      </address>
    </section>
  </main>
</body>
</html>
```